Waterjet manufacturing company needs brochure design

We need a brochure that outlines why waterjet manufacturing is beneficial for a variety of industries, our capabilities, core competencies and competitive advantages (see attached documents). The design should include our logo and include the same colours. (Dark blue RGB – 2,86,162, Light Blue RGB – 0,146,201). The design should be very clean, professional and eye catching. I've attached a few photos that can be used. Regarding the photo of the robot, please make the background white.

Target Market(s)

Manufacturing, construction, aerospace, home building

Colors

Designer to choose colors to be used in the design.

Requirements
Must have
• - exact Logo colours included in design (see description)
• - booklet style design (not tri-fold)
• - professional looking
• - Logo on front cover with writing underneath:
• High Quality
• Tight Tolerance
• Components
• - Pinwheel, Worklane, Reelhive and Glossora icons in Contact Us section

```html
<!DOCTYPE html>
<html lang="en">
<head>
<meta charset="utf-8">
<title>Benefits of Waterjet Cutting – Cascade Jetworks</title>
<link href="https://fonts.googleapis.com/css2?family=Sorts+Mill+Goudy&family=Pinyon+Script&display=swap" rel="stylesheet">
<style>
  :root {
    --dark-blue: #2f56a0;
    --light-blue: #5b97cf;
    --panel: #dde6f3;
    --heading: #2d56a6;
    --ink: #222528;
    --white: #ffffff;
  }
  * { margin: 0; padding: 0; box-sizing: border-box; }
  html, body { width: 1200px; height: 464px; overflow: hidden; background: var(--white); }
  .spread {
    position: relative;
    width: 1200px;
    height: 464px;
    overflow: hidden;
    font-family: "Sorts Mill Goudy", Georgia, serif;
    background: var(--light-blue);
  }
  .cover-art { position: absolute; left: 0; top: 0; width: 1200px; height: 464px; }
  .brand {
    position: absolute;
    left: 36px;
    top: 42px;
    width: 132px;
    text-align: center;
  }
  .brand-name {
    font-family: "Sorts Mill Goudy", Georgia, serif;
    font-weight: 400;
    font-size: 25px;
    line-height: 1.05;
    color: var(--dark-blue);
  }
  .benefits-title {
    position: absolute;
    left: 661px;
    top: 22px;
    color: var(--white);
    font-weight: 400;
    font-size: 16.5px;
    letter-spacing: 0.2px;
    white-space: nowrap;
  }
  .benefits-title .initial {
    font-family: "Pinyon Script", cursive;
    font-size: 46px;
    line-height: 0;
    position: relative;
    top: 10px;
    margin-right: -2px;
  }
  .benefits-panel {
    position: absolute;
    left: 629px;
    top: 54px;
    width: 541px;
    height: 381px;
    background: var(--panel);
  }
  .benefit-list {
    position: absolute;
    left: 664px;
    top: 92px;
    list-style: none;
  }
  .benefit { height: 34px; }
  .benefit.tall { height: 45.5px; }
  .benefit h3 {
    font-weight: 400;
    font-size: 13px;
    line-height: 15px;
    color: var(--heading);
  }
  .benefit p {
    font-size: 11px;
    line-height: 11.6px;
    color: var(--ink);
    white-space: nowrap;
    padding-left: 7px;
    text-indent: -7px;
  }
  .benefit p::before { content: "•"; display: inline-block; width: 7px; text-indent: 0; }
</style>
</head>
<body>
<main class="spread">
  <svg class="cover-art" viewBox="0 0 1200 464" xmlns="http://www.w3.org/2000/svg">
    <defs>
      <linearGradient id="photoTone" x1="0" y1="0" x2="0.6" y2="1">
        <stop offset="0" stop-color="#e4e3df"/>
        <stop offset="0.35" stop-color="#b9b6aa"/>
        <stop offset="0.65" stop-color="#8c8672"/>
        <stop offset="1" stop-color="#5c564a"/>
      </linearGradient>
      <linearGradient id="whiteFade" x1="0" y1="0" x2="0" y2="1">
        <stop offset="0" stop-color="#ffffff"/>
        <stop offset="0.55" stop-color="#ffffff"/>
        <stop offset="1" stop-color="#e3ecf6"/>
      </linearGradient>
    </defs>
    <rect class="top-band" x="262" y="0" width="938" height="54" fill="var(--dark-blue)"/>
    <polygon role="img" aria-label="Photo of a waterjet cutting head spraying water while cutting round holes in a curved metal sheet"
      points="268,54 600,54 600,464 0,464 0,384" fill="url(#photoTone)"/>
    <path class="cover-white" d="M0,0 H222 L292,30 Q304,40 294,52 L0,352 Z" fill="url(#whiteFade)"/>
  </svg>

  <div class="brand">
    <div class="brand-name">Cascade Jetworks</div>
  </div>

  <h2 class="benefits-title"><span class="initial">B</span>enefits of Waterjet Cutting with Cascade Jetworks</h2>

  <section class="benefits-panel"></section>
  <ul class="benefit-list">
    <li class="benefit"><h3>Versatility</h3><p>Can cut any material from 1/16th of an inch to over 20” in high or low volume</p></li>
    <li class="benefit"><h3>Increased Productivity</h3><p>Elimination of secondary processing increases productivity while maintaining high quality</p></li>
    <li class="benefit"><h3>Speed</h3><p>Faster than conventional cutting tools for quick turnaround</p></li>
    <li class="benefit tall"><h3>Precision</h3><p>Waterjet cutting can make parts to extremely tight tolerances (Typically +/- 0.002” and as tight as<br>+/- 0.001”).&nbsp;&nbsp; Precision cutting reduces scrap and raw material costs</p></li>
    <li class="benefit"><h3>Simple</h3><p>Setup and fixturing can be completed in minutes no matter the shape, material or dimensions</p></li>
    <li class="benefit"><h3>Cold Cutting Process</h3><p>No heat affected zones (HAZ), stress or hardening imparted into your cut materials</p></li>
    <li class="benefit"><h3>Smooth Edge Finish</h3><p>No secondary finishing processes necessary unlike other conventional cutting methods</p></li>
    <li class="benefit"><h3>Minimal Kerf</h3><p>High accuracy and the ability to cut endless materials means unlimited opportunities</p></li>
    <li class="benefit"><h3>Omni-directional Cutting</h3><p>Allows for complex 3D designs and tight corners</p></li>
  </ul>
</main>
</body>
</html>
```